RW Framewell Inc Business cards

We need business cards using our existing logo but slightly modified. Right now the logo says RW Loadbearing Masonry. We want to keep the RW part of the design, but replace the Structural Concrete portion with "FRAMEWELL". Please see the attached file.
Ideally this would be a blank template so we can add Different Names, titles, and phone numbers later.
On the one side we want only the logo and on the other side the detail. I'm attaching an example for you to see.
Please reach out with any other questions. Our address and other details will be given out once we find a design we like.

Target Market(s)

Construction Industry

```html
<!DOCTYPE html>
<html lang="en">
<head>
<meta charset="utf-8">
<title>RW Framewell Inc — Business Cards</title>
<link rel="stylesheet" href="https://fonts.googleapis.com/css2?family=Roboto:wght@400;500;700&display=swap">
<style>
  :root {
    --backdrop: #5b80b9;
    --brand-blue: #2f5fa3;
    --brand-blue-deep: #24508f;
    --card-white: #f4f4f4;
    --ink-grey: #555a60;
    --soft-grey: #e3e3e3;
    --edge-grey: #8a8c90;
    --band-text: #ffffff;
  }
  html, body {
    margin: 0;
    width: 1200px;
    height: 852px;
    overflow: hidden;
    background: var(--backdrop);
    font-family: "Roboto", Arial, sans-serif;
  }
  .stage {
    position: relative;
    width: 1200px;
    height: 852px;
  }
  .card {
    position: absolute;
    width: 520px;
    height: 300px;
    border-radius: 24px;
    overflow: hidden;
    box-shadow: 0 6px 18px rgba(20, 40, 80, 0.35);
  }
  /* Logo side */
  .card--back {
    left: 60px;
    top: 120px;
    background: var(--brand-blue);
  }
  .card--back .wordmark {
    position: absolute;
    left: 0;
    right: 0;
    top: 78px;
    text-align: center;
    color: var(--brand-blue-deep);
    font-weight: 700;
  }
  .wordmark__initials {
    display: block;
    font-size: 96px;
    line-height: 1;
    letter-spacing: 2px;
  }
  .wordmark__name {
    display: block;
    font-size: 26px;
    letter-spacing: 9px;
    margin-top: 6px;
  }
  /* Detail side */
  .card--front {
    left: 620px;
    top: 420px;
    background: var(--card-white);
  }
  .card--front .wordmark {
    position: absolute;
    left: 36px;
    top: 34px;
    color: var(--brand-blue);
    font-weight: 700;
  }
  .card--front .wordmark__initials { font-size: 70px; }
  .card--front .wordmark__name { font-size: 19px; letter-spacing: 6px; margin-top: 4px; }
  .faint-initials {
    position: absolute;
    right: 20px;
    top: 10px;
    font-size: 170px;
    font-weight: 700;
    color: var(--soft-grey);
    line-height: 1;
  }
  .holder {
    position: absolute;
    left: 36px;
    bottom: 34px;
  }
  .holder__name {
    margin: 0;
    font-size: 21px;
    font-weight: 700;
    color: var(--brand-blue);
  }
  .holder__title {
    margin: 3px 0 0;
    font-size: 13px;
    color: var(--ink-grey);
  }
  .contact {
    position: absolute;
    left: 290px;
    top: 140px;
    margin: 0;
    padding: 0;
    list-style: none;
    font-size: 12px;
    color: var(--ink-grey);
    line-height: 1.55;
  }
  .contact li { display: flex; align-items: flex-start; gap: 7px; }
  .contact svg { width: 11px; height: 11px; margin-top: 3px; flex: none; fill: var(--brand-blue); }
  .contact .no-icon { padding-left: 18px; }
  .web-band {
    position: absolute;
    right: 0;
    bottom: 14px;
    width: 250px;
    height: 40px;
    background: var(--brand-blue);
    border-top-left-radius: 18px;
    color: var(--band-text);
    font-size: 13px;
    font-weight: 700;
    display: flex;
    align-items: center;
    justify-content: center;
  }
  .edge-strip {
    position: absolute;
    left: 0;
    right: 0;
    bottom: 0;
    height: 14px;
    background: var(--edge-grey);
  }
</style>
</head>
<body>
<main class="stage">
  <section class="card card--back" aria-label="Logo side">
    <div class="wordmark">
      <span class="wordmark__initials">RW</span>
      <span class="wordmark__name">FRAMEWELL</span>
    </div>
  </section>

  <section class="card card--front" aria-label="Detail side">
    <span class="faint-initials" aria-hidden="true">RW</span>
    <div class="wordmark">
      <span class="wordmark__initials">RW</span>
      <span class="wordmark__name">FRAMEWELL</span>
    </div>
    <ul class="contact">
      <li>
        <svg viewBox="0 0 24 24" aria-hidden="true"><path d="M6.6 10.8a15 15 0 0 0 6.6 6.6l2.2-2.2a1 1 0 0 1 1-.25 11.4 11.4 0 0 0 3.6.57 1 1 0 0 1 1 1V20a1 1 0 0 1-1 1A17 17 0 0 1 3 4a1 1 0 0 1 1-1h3.5a1 1 0 0 1 1 1c0 1.25.2 2.45.57 3.6a1 1 0 0 1-.25 1z"/></svg>
        555-014-2290
      </li>
      <li>
        <svg viewBox="0 0 24 24" aria-hidden="true"><path d="M2 5h20v14H2z M3 6l9 7 9-7" /></svg>
        evan@rwframewell.com
      </li>
      <li class="no-icon">88 Timber Row, Millbrook,</li>
      <li class="no-icon">California, US 95012</li>
    </ul>
    <div class="holder">
      <p class="holder__name">Evan RW Hale</p>
      <p class="holder__title">Managing Director</p>
    </div>
    <div class="web-band">www.rwframewell.com</div>
    <div class="edge-strip"></div>
  </section>
</main>
</body>
</html>
```